Residential real estate home builder in west texas

We need a website design for our home building business based in west Texas called Birch Hollow homes. We build new construction for potential homeowners in Amarillo. Currently we do not have any completed construction, but we have floor plans and architectural drawings of the front elevation. The website would need to be able to properly advertise a architectural drawing, floor plans, and descriptive content at the initial phase. The website will need to be simple but professional with generic picture content.
The website will need the ability to be updated in the future for the additions of home pictures, and video content and virtual tours of the homes.

Target Market(s)

Potential Home buyers

Industry/Entity Type

Real Estate

Number of Pages Required

5+ page

Font styles to use
Sans Serif

Colors
f37122
757575

Requirements
Must have
• Web design must be simple and easy to navigate. There is not much picture content, so it will need to be simple.
• 5 pages:
• Home, Available homes, Available floor plans, guide to ownership, Contact
• The website will need the ability to be updated in the future for the additions of pictures, and video content of the homes when they are built. ( A virtual tour).
Nice to have
• I would like to see a modern and cohesive design. Contact information at the bottom of each page.
Should not have
• A Black background

```html
<!DOCTYPE html>
<html lang="en">
<head>
<meta charset="utf-8">
<title>Birch Hollow Homes</title>
<link href="https://fonts.googleapis.com/css2?family=Mulish:wght@300;400;600;700&display=swap" rel="stylesheet">
<style>
:root{
  --orange:#f37122;
  --orange-deep:#e85d22;
  --grey:#757575;
  --grey-dark:#5e5e5e;
  --footer:#6e6e6e;
  --footer-bar:#5b5b5b;
  --ink:#333;
  --light:#f2f2f2;
  --white:#fff;
}
*{box-sizing:border-box;margin:0;padding:0}
html,body{width:1200px;height:3403px;overflow:hidden}
body{font-family:"Mulish",sans-serif;color:var(--ink);background:var(--white);position:relative}
.abs{position:absolute}
a{color:inherit;text-decoration:none}

/* header */
.site-header{left:0;top:0;width:1200px;height:113px;background:var(--white)}
.brand{left:92px;top:26px;color:var(--grey);font-weight:600;text-align:center;line-height:1}
.brand-name{font-size:36px;letter-spacing:-0.5px}
.brand-sub{font-size:17px;letter-spacing:8px;margin-top:4px}
.main-nav{left:392px;top:46px;display:flex;gap:34px;font-size:18px;color:var(--grey)}
.main-nav .active{color:var(--orange)}

/* hero */
.hero{left:0;top:113px;width:1200px;height:567px;background:linear-gradient(160deg,#9fc2e3 0%,#dfe7ee 35%,#c9c6c0 60%,#6f7558 85%,#4e5540 100%)}
.hero-title{left:109px;top:192px;color:var(--white);font-size:47px;font-weight:400;line-height:1.08;letter-spacing:1px}
.btn{display:inline-block;font-size:15px;letter-spacing:1px;text-transform:uppercase;text-align:center}
.btn-dark{background:linear-gradient(#7a7a7a,#4e4e4e);color:var(--white)}
.hero .btn-dark{position:absolute;left:109px;top:309px;width:170px;height:44px;line-height:44px}
.dots{left:555px;top:531px;display:flex;gap:9px}
.dots span{width:13px;height:13px;border-radius:50%;background:var(--white)}
.dots span:first-child{background:transparent;border:2px solid var(--white)}

/* about */
.about{left:0;top:680px;width:1200px;height:377px;background:linear-gradient(#a8745b 0%,#d36a3a 45%,var(--orange-deep) 100%);color:var(--white);text-align:center}
.section-title{font-size:33px;font-weight:400;letter-spacing:.5px}
.about .section-title{position:absolute;left:0;top:70px;width:1200px}
.about .rule{position:absolute;left:560px;top:120px;width:80px;height:2px;background:var(--white)}
.about-copy{position:absolute;left:186px;top:134px;width:828px;font-size:14px;line-height:1.6}
.about-copy p+p{margin-top:12px}
.btn-outline{border:2px solid var(--white);color:var(--white)}
.about .btn-outline{position:absolute;left:522px;top:286px;width:158px;height:38px;line-height:34px}

/* architectural */
.arch{left:0;top:1057px;width:1200px;height:517px;background:var(--light);border-bottom:1px solid #ddd}
.arch-media{left:0;top:0;width:700px;height:517px;background:linear-gradient(90deg,#d9d6cf 0%,#e6e4df 55%,#f2f2f2 100%)}
.arch-title{left:628px;top:123px;font-size:32px;font-weight:300;line-height:1.1;color:#555;letter-spacing:1px}
.arch-copy{left:628px;top:206px;width:545px;font-size:13.5px;line-height:1.65;color:#666}
.arch-copy p+p{margin-top:14px}
.arch .btn-dark{position:absolute;left:628px;top:372px;width:168px;height:47px;line-height:47px}

/* featured */
.featured{left:0;top:1574px;width:1200px;height:531px}
.featured .section-title{position:absolute;left:0;top:55px;width:1200px;text-align:center;color:#444;font-size:29px}
.featured .rule{position:absolute;left:560px;top:102px;width:80px;height:2px;background:var(--orange)}
.card{top:134px;width:311px;height:347px;background:var(--white);box-shadow:0 0 6px rgba(0,0,0,.18)}
.card-media{height:190px}
.card h3{font-size:19px;font-weight:400;color:#444;margin:18px 0 0 32px}
.card p{font-size:13px;line-height:1.55;color:#777;margin:8px 24px 0 32px}
.card .more{display:block;font-size:12px;font-weight:700;color:var(--orange);margin:12px 0 0 32px}
.arrow{top:280px}

/* virtual tours */
.tours{left:0;top:2105px;width:1200px;height:476px;background:linear-gradient(180deg,#7fa8d8 0%,#bfd4ea 35%,#c9c8c3 60%,#5f7048 100%)}
.tours-shape{left:0;top:0}
.tours-title{left:100px;top:124px;color:var(--white);font-size:32px;font-weight:400;line-height:1.1}
.tours-copy{left:100px;top:200px;width:400px;font-size:14px;line-height:1.6;color:var(--white)}
.tours .btn-outline{position:absolute;left:102px;top:347px;width:166px;height:40px;line-height:36px}
.play{left:810px;top:197px}

/* floor plans */
.plans{left:0;top:2581px;width:1200px;height:469px}
.plans-media{left:100px;top:75px;width:501px;height:315px;background:linear-gradient(170deg,#e7ecf0 0%,#d8d8d4 55%,#8d9480 100%)}
.plans-title{left:651px;top:88px;font-size:32px;font-weight:400;color:#444;letter-spacing:.5px}
.plans-copy{left:651px;top:141px;width:500px;font-size:13.5px;line-height:1.65;color:#666}
.plans-copy p+p{margin-top:14px}
.btn-orange{background:var(--orange-deep);color:var(--white)}
.plans .btn-orange{position:absolute;left:651px;top:331px;width:143px;height:41px;line-height:41px}

/* footer */
.site-footer{left:0;top:3050px;width:1200px;height:284px;background:var(--footer);color:var(--white)}
.foot-col{top:73px}
.foot-col h4{font-size:16px;font-weight:400;letter-spacing:.5px;margin-bottom:14px}
.foot-col li{list-style:none;font-size:13.5px;line-height:30px}
.contact-line{display:flex;align-items:center;gap:8px}
.social{display:flex;gap:8px;margin-top:2px}
.social span{width:36px;height:36px;border-radius:50%;border:2px solid var(--white)}
.foot-brand{left:896px;top:168px;text-align:center;font-weight:600;color:var(--white);line-height:1}
.foot-brand .brand-name{font-size:33px}
.foot-brand .brand-sub{font-size:15px;letter-spacing:7px}
.footer-bar{left:0;top:3334px;width:1200px;height:69px;background:var(--footer-bar);color:#bbb;font-size:12px;text-align:center;line-height:69px}
</style>
</head>
<body>

<header class="site-header abs">
  <div class="brand abs">
    <div class="brand-name">BIRCH HOLLOW</div>
    <div class="brand-sub">HOMES</div>
  </div>
  <nav class="main-nav abs">
    <a class="active" href="#">Home</a>
    <a href="#">Available homes</a>
    <a href="#">Available floor plans</a>
    <a href="#">Guide to ownership</a>
    <a href="#">Contact</a>
  </nav>
</header>

<section class="hero abs" role="img" aria-label="Photo of a modern white two-storey house with a landscaped front yard under a blue sky">
  <h1 class="hero-title abs">HOME CONSTRUCTION<br>&amp; FLOOR PLANS</h1>
  <a class="btn btn-dark" href="#">View homes</a>
  <div class="dots abs"><span></span><span></span><span></span><span></span></div>
</section>

<section class="about abs">
  <h2 class="section-title">ABOUT BIRCH HOLLOW HOMES</h2>
  <div class="rule"></div>
  <div class="about-copy">
    <p>We design and build new homes across West Texas with care for every detail, from the first sketch to the final walk-through. Our plans balance open living spaces, quality materials and honest pricing so families in Amarillo can move into a home made to last.</p>
    <p>Every build starts with a conversation about how you live. We guide you through lots, floor plans and finishes, and keep you informed at each step of construction.</p>
  </div>
  <a class="btn btn-outline" href="#">Read more</a>
</section>

<section class="arch abs">
  <div class="arch-media abs" role="img" aria-label="Photo of hands drafting an architectural drawing with a ruler, pencil and rolled blueprints"></div>
  <h2 class="arch-title abs">ARCHITECTURAL<br>DRAWING</h2>
  <div class="arch-copy abs">
    <p>See each home before it is built. Our front elevation drawings show rooflines, materials and proportions so you know exactly what to expect.</p>
    <p>Browse detailed renderings for every plan we offer, compare styles side by side and choose the exterior that suits your street, your lot and your taste.</p>
  </div>
  <a class="btn btn-dark" href="#">View homes</a>
</section>

<section class="featured abs">
  <h2 class="section-title">FEATURED HOMES</h2>
  <div class="rule"></div>
  <svg class="arrow abs" style="left:76px" width="24" height="56" viewBox="0 0 24 56" aria-hidden="true"><polyline points="20,2 4,28 20,54" fill="none" stroke="#888" stroke-width="2"/></svg>
  <article class="card abs" style="left:116px">
    <div class="card-media" role="img" aria-label="Photo of a white modern home with a grey garage" style="background:linear-gradient(170deg,#dfe6ec,#b9bdb5 60%,#59604d)"></div>
    <h3>Home Title here</h3>
    <p>Three bedrooms, two baths and an open kitchen facing a shaded back patio.</p>
    <a class="more" href="#">READ MORE</a>
  </article>
  <article class="card abs" style="left:442px">
    <div class="card-media" role="img" aria-label="Photo of a white contemporary home with a paved driveway" style="background:linear-gradient(170deg,#b9d1ea,#e3e3e0 55%,#8c857a)"></div>
    <h3>Home Title here</h3>
    <p>Four bedrooms with a bright living room, study nook and a wide double garage.</p>
    <a class="more" href="#">READ MORE</a>
  </article>
  <article class="card abs" style="left:769px">
    <div class="card-media" role="img" aria-label="Photo of a grey sided family home with a front porch" style="background:linear-gradient(170deg,#c6cdd3,#8d949a 55%,#6f7a52)"></div>
    <h3>Home Title here</h3>
    <p>Classic porch plan with a split master suite and a large family dining area.</p>
    <a class="more" href="#">READ MORE</a>
  </article>
  <svg class="arrow abs" style="left:1100px" width="24" height="56" viewBox="0 0 24 56" aria-hidden="true"><polyline points="4,2 20,28 4,54" fill="none" stroke="#888" stroke-width="2"/></svg>
</section>

<section class="tours abs" role="img" aria-label="Photo of a modern two-storey home with stone cladding and palm trees">
  <svg class="tours-shape abs" width="1200" height="476" viewBox="0 0 1200 476" aria-hidden="true">
    <polygon points="0,0 533,0 680,476 0,476" fill="#ec6a2c"/>
  </svg>
  <h2 class="tours-title abs">VIRTUAL TOURS OF<br>THE HOMES</h2>
  <p class="tours-copy abs">Walk through our homes from your couch. Virtual tours let you explore every room, check the flow between spaces and picture your furniture in place before you ever visit a site in person.</p>
  <a class="btn btn-outline" href="#">Read more</a>
  <svg class="play abs" width="106" height="106" viewBox="0 0 106 106" aria-label="Play video"><circle cx="53" cy="53" r="52" fill="rgba(255,255,255,.55)"/><polygon points="42,33 76,53 42,73" fill="#fff"/></svg>
</section>

<section class="plans abs">
  <div class="plans-media abs" role="img" aria-label="Photo of a white modern townhouse with balconies"></div>
  <h2 class="plans-title abs">FLOOR PLANS</h2>
  <div class="plans-copy abs">
    <p>Compare layouts, square footage and room counts across every plan we build, then save the ones that fit your family best.</p>
    <p>Each plan can be adjusted with extra bedrooms, larger garages or covered patios to match the way you want to live.</p>
  </div>
  <a class="btn btn-orange" href="#">Read more</a>
</section>

<footer class="site-footer abs">
  <div class="foot-col abs" style="left:100px">
    <h4>COMPANY</h4>
    <ul><li>Home</li><li>Available homes</li><li>Available floor plans</li><li>Guide to ownership</li></ul>
  </div>
  <div class="foot-col abs" style="left:288px">
    <h4>RESOURCES</h4>
    <ul><li>Help</li><li>FAQ</li><li>Sitemap</li><li>Term of Use</li></ul>
  </div>
  <div class="foot-col abs" style="left:460px">
    <h4>SUPPORT</h4>
    <ul><li>Support</li><li>News &amp; Blogs</li><li>Clients</li><li>Contact Us</li></ul>
  </div>
  <div class="foot-col abs" style="left:621px">
    <h4>CONTACT US</h4>
    <ul>
      <li class="contact-line"><svg width="14" height="18" viewBox="0 0 14 18" aria-hidden="true"><path d="M7 0C3 0 0 3 0 7c0 5 7 11 7 11s7-6 7-11c0-4-3-7-7-7zm0 10a3 3 0 110-6 3 3 0 010 6z" fill="#fff"/></svg>2418 Mesa Ridge Drive, Amarillo TX 79101</li>
      <li class="contact-line"><svg width="16" height="16" viewBox="0 0 16 16" aria-hidden="true"><path d="M3 1l3 3-2 2c1 2 3 4 6 6l2-2 3 3-2 2C7 15 1 9 1 3z" fill="none" stroke="#fff" stroke-width="1.4"/></svg>806.555.0142</li>
      <li class="contact-line"><svg width="16" height="12" viewBox="0 0 16 12" aria-hidden="true"><rect x="0.7" y="0.7" width="14.6" height="10.6" fill="none" stroke="#fff" stroke-width="1.4"/><polyline points="1,1 8,7 15,1" fill="none" stroke="#fff" stroke-width="1.4"/></svg>hello@birchhollowhomes.com</li>
    </ul>
  </div>
  <div class="foot-col abs" style="left:934px">
    <h4>FOLLOW US</h4>
    <div class="social"><span></span><span></span><span></span><span></span></div>
  </div>
  <div class="foot-brand abs">
    <div class="brand-name">BIRCH HOLLOW</div>
    <div class="brand-sub">HOMES</div>
  </div>
</footer>
<div class="footer-bar abs">© 2017 Birch Hollow Homes. All right reserved</div>

</body>
</html>
```